We need a new business card that reflects who we are. Professional, classy, modern, and service ori

We need a business card design for a window coverings design company in Kansas City called Bright Lane Interiors. We offer professional, modern, and high quality window covering products. We are looking to portray an image of a big, national franchise. We are a 5 location (with showrooms) business with 10 professional designers and 4 professional installers. These cards will be used with Thank you cards, given to realtors, and asked for referrals with.

Target Market(s)

Kansas City

Industry/Entity Type

Business

Contact Information for Business Card

We would like our card to look clean and simple on the front, featuring our logo and Marlow Fenwick's. Our designers' phone numbers and emails should be displayed as well as their title.

Font styles to use
Sans Serif

Colors

Designer to choose colors to be used in the design.

Requirements
Must have
• Front - Logos, name, phone number, email address
• Back - Showroom locations, social media? Appt date/time?
Nice to have
• I would like a clean and modern look (not contemporary. I like a white background, but I am open to ideas. Looking for a "National chain" look for a small business.
Should not have
• Too much busyness.

```html
<!DOCTYPE html>
<html lang="en">
<head>
<meta charset="utf-8">
<title>Bright Lane Interiors – Business Card</title>
<link href="https://fonts.googleapis.com/css2?family=Lato:wght@400;700&family=Playfair+Display:wght@400;700&display=swap" rel="stylesheet">
<style>
  :root {
    --brand-red: #c9434a;
    --slate-grey: #8e9196;
    --ink: #1f1f1f;
    --text-grey: #3a3a3a;
    --paper: #ffffff;
    --backdrop: #ecebe8;
    --social-blue: #3b7fc4;
    --faint-rule: #555555;
  }
  * { box-sizing: border-box; margin: 0; padding: 0; }
  html, body { width: 1200px; height: 900px; overflow: hidden; }
  body {
    background: var(--backdrop);
    font-family: "Lato", sans-serif;
    position: relative;
  }
  .card {
    position: absolute;
    width: 560px;
    height: 320px;
    background: var(--paper);
    box-shadow: 0 6px 18px rgba(0,0,0,0.18);
    overflow: hidden;
  }

  /* Back of card */
  .card-back { left: 120px; top: 110px; }
  .back-header {
    height: 96px;
    background: var(--brand-red);
    display: flex;
    align-items: center;
    justify-content: center;
  }
  .back-title {
    font-family: "Lato", sans-serif;
    font-weight: 400;
    font-size: 34px;
    letter-spacing: 0.5px;
    color: var(--paper);
  }
  .appointment {
    height: 84px;
    padding: 16px 0 0 170px;
  }
  .appointment-line {
    display: flex;
    align-items: flex-end;
    font-size: 15px;
    color: var(--ink);
    text-transform: uppercase;
    height: 30px;
  }
  .appointment-line .blank {
    display: inline-block;
    width: 270px;
    border-bottom: 1px dashed var(--faint-rule);
    margin-left: 4px;
    margin-bottom: 3px;
  }
  .back-footer {
    height: 140px;
    background: var(--slate-grey);
    color: var(--paper);
    text-align: center;
    padding-top: 22px;
  }
  .showroom-heading {
    font-size: 15px;
    letter-spacing: 0.6px;
    text-transform: uppercase;
    margin-bottom: 24px;
  }
  .showroom-list {
    list-style: none;
    display: flex;
    justify-content: center;
    gap: 10px;
    font-size: 16px;
  }
  .showroom-list li + li::before {
    content: "";
    display: inline-block;
    width: 7px; height: 7px;
    border-radius: 50%;
    background: var(--paper);
    margin-right: 10px;
    vertical-align: middle;
  }

  /* Front of card */
  .card-front { left: 520px; top: 470px; }
  .brand-block {
    position: absolute;
    right: 34px;
    top: 42px;
    text-align: center;
  }
  .brand-mark-dot {
    width: 40px; height: 40px;
    background: var(--brand-red);
    margin: 0 auto 10px;
  }
  .brand-name {
    font-family: "Lato", sans-serif;
    font-weight: 400;
    font-size: 24px;
    color: var(--ink);
  }
  .brand-tagline {
    font-family: "Playfair Display", serif;
    font-size: 11px;
    color: var(--ink);
    margin-top: 2px;
  }
  .partner {
    position: absolute;
    right: 40px;
    top: 168px;
    text-align: right;
  }
  .partner-name {
    display: flex;
    align-items: center;
    justify-content: flex-end;
    gap: 6px;
    font-weight: 700;
    font-size: 16px;
    color: #555a60;
  }
  .partner-badge {
    width: 16px; height: 16px;
    border-radius: 50%;
    background: #e59a3c;
  }
  .social-links {
    display: flex;
    justify-content: flex-end;
    gap: 5px;
    margin-top: 10px;
  }
  .social-links span {
    width: 18px; height: 18px;
    border-radius: 50%;
    background: var(--social-blue);
  }
  .accent {
    position: absolute;
    left: 0;
    width: 30px;
    height: 34px;
  }
  .accent-red { top: 180px; background: var(--brand-red); }
  .accent-grey { top: 250px; background: var(--slate-grey); }
  .contact {
    position: absolute;
    left: 52px;
    top: 158px;
  }
  .person-name {
    font-family: "Playfair Display", serif;
    font-weight: 700;
    font-size: 20px;
    text-transform: uppercase;
    letter-spacing: 0.3px;
  }
  .person-name .first { color: var(--brand-red); }
  .person-name .last { color: var(--ink); }
  .person-title {
    font-size: 16px;
    color: var(--text-grey);
    margin-bottom: 22px;
  }
  .contact-row {
    display: flex;
    align-items: center;
    gap: 8px;
    font-size: 17px;
    color: var(--text-grey);
    line-height: 26px;
  }
  .contact-row svg { width: 14px; height: 14px; fill: var(--brand-red); flex: none; }
</style>
</head>
<body>

  <section class="card card-back" aria-label="Business card back">
    <header class="back-header">
      <h1 class="back-title">Bright Lane Interiors</h1>
    </header>
    <div class="appointment">
      <p class="appointment-line">Date<span class="blank"></span></p>
      <p class="appointment-line">Time<span class="blank"></span></p>
    </div>
    <footer class="back-footer">
      <h2 class="showroom-heading">Showroom Locations</h2>
      <ul class="showroom-list">
        <li>Location 1</li>
        <li>Location 2</li>
        <li>Location 3</li>
        <li>Location 4</li>
        <li>Location 5</li>
      </ul>
    </footer>
  </section>

  <section class="card card-front" aria-label="Business card front">
    <div class="brand-block">
      <div class="brand-mark-dot"></div>
      <p class="brand-name">Bright Lane Interiors</p>
      <p class="brand-tagline">Blinds, Shades, Shutters, Draperies &amp; Decor</p>
    </div>

    <div class="partner">
      <p class="partner-name">Marlow Fenwick <span class="partner-badge"></span></p>
      <div class="social-links" aria-label="Social media">
        <span></span><span></span><span></span><span></span>
      </div>
    </div>

    <div class="accent accent-red"></div>
    <div class="accent accent-grey"></div>

    <div class="contact">
      <p class="person-name"><span class="first">Daniel</span> <span class="last">Hartley</span></p>
      <p class="person-title">Managing Director</p>
      <p class="contact-row">
        <svg viewBox="0 0 16 16" aria-hidden="true"><path d="M3.6 1.5l2.3 2.6-1.3 1.7c.9 2 2.5 3.6 4.6 4.6l1.7-1.3 2.6 2.3-1.6 2.1C6.8 13 3 9.2 1.5 3.1z"/></svg>
        444 555 0192
      </p>
      <p class="contact-row">
        <svg viewBox="0 0 16 16" aria-hidden="true"><path d="M1 3h14v10H1z M2 4.2v.4l6 4 6-4v-.4z" fill-rule="evenodd"/></svg>
        info@brightlaneinteriors.com
      </p>
    </div>
  </section>

</body>
</html>
```